Label Design Refresh for existing High End Supplement line

Design a label for our high end supplement brand, packaged in a Cobal Blue bottle.... using Clear labels as the label stock media.

A clear label design will take advantage of the blue bottle and can incorporate any design element you create, metalic elements, new graphics etc.

our line spans 50 different product categories and over 400 unique SKUs, so any elements you suggest to differentiate products or categories will be appreciated.

see: www.velandrahealth.com
Updates

Need designers to meet project requirements. Full label, clear label stock design (clear background with exception for design elements and text etc.)

Target Market(s)

Men and Women 25-55 Health conscious and not price sensitive. Product is 5x higher cost than competition.

Industry/Entity Type

Sexual health for men and women. testosterone, hormone health, nootropics

Font styles to use
Sans Serif

Colors

Designer to choose colors to be used in the design.

Requirements
Must have
• Clear label design for Cobalt blue, packer style, pharma bottle. Must feature Velandra brand on front panel. Must show entire label panel design as 2.8in x 7.25in. Graphics can be full color with metalic or foil type elements.
Nice to have
• Name of products include: SHBG, Testosterone & Libido, Vitalis Restore Phase 3, LH Formula, ADHD Phase1,
Should not have
• Busy designs that are stock images for supplement label layouts

```html
<!DOCTYPE html>
<html lang="en">
<head>
<meta charset="utf-8">
<title>Velandra Vitalis Restore Phase 3 – Label</title>
<link href="https://fonts.googleapis.com/css2?family=Barlow:wght@500;700&family=Barlow+Semi+Condensed:wght@400;500&display=swap" rel="stylesheet">
<style>
  :root {
    --page: #f4f5f8;
    --cobalt: #1f2fa8;
    --cobalt-deep: #141c7a;
    --cobalt-light: #3a4fd0;
    --ink: #ffffff;
    --ink-soft: #e8ebff;
    --gold: #e7cf6e;
    --gold-light: #f6ecb4;
    --gold-deep: #c9a93a;
  }
  * { margin: 0; padding: 0; box-sizing: border-box; }
  html, body { width: 1200px; height: 1200px; overflow: hidden; }
  body {
    background: var(--page);
    font-family: "Barlow", sans-serif;
    color: var(--ink);
    position: relative;
  }
  .label {
    position: absolute;
    left: 262px; top: 110px;
    width: 675px; height: 980px;
    background: linear-gradient(100deg, var(--cobalt-light) 0%, var(--cobalt) 35%, var(--cobalt-deep) 100%);
    border-radius: 10px;
    overflow: hidden;
  }
  .brand {
    position: absolute;
    left: 58px; top: 855px;
    transform: rotate(-90deg);
    transform-origin: 0 0;
    width: 715px;
    font-weight: 700;
    font-size: 104px;
    line-height: 90px;
    letter-spacing: 2px;
    color: var(--ink);
    white-space: nowrap;
  }
  .product-name {
    position: absolute;
    left: 198px; top: 190px;
    font-weight: 700;
    font-size: 92px;
    line-height: 1;
    letter-spacing: 1px;
  }
  .product-phase {
    position: absolute;
    left: 200px; top: 278px;
    font-family: "Barlow Semi Condensed", sans-serif;
    font-weight: 500;
    font-size: 34px;
    letter-spacing: 1px;
    color: var(--ink-soft);
  }
  .features {
    position: absolute;
    left: 206px; top: 386px;
    list-style: none;
    font-family: "Barlow Semi Condensed", sans-serif;
    font-weight: 400;
    font-size: 24px;
    line-height: 28px;
    letter-spacing: 0.5px;
    color: var(--ink-soft);
  }
  .features li { position: relative; padding-left: 28px; margin-bottom: 2px; }
  .features li::before {
    content: "";
    position: absolute; left: 0; top: 7px;
    width: 16px; height: 16px;
    border-radius: 2px 10px 2px 10px;
    background: linear-gradient(135deg, var(--gold-light), var(--gold-deep));
  }
  .brain-art {
    position: absolute;
    left: 462px; top: 545px;
    width: 200px; height: 260px;
    border-radius: 46% 46% 40% 40%;
    background: radial-gradient(circle at 45% 40%, rgba(246,236,180,0.30), rgba(201,169,58,0.12) 70%, transparent 100%);
  }
  .supplement-type {
    position: absolute;
    left: 195px; top: 682px;
    font-weight: 700;
    font-size: 36px;
    line-height: 40px;
    letter-spacing: 1px;
  }
  .rule {
    position: absolute;
    left: 197px; top: 776px;
    width: 232px; height: 2px;
    background: var(--ink);
  }
  .count {
    position: absolute;
    left: 195px; top: 800px;
    display: flex; align-items: center; gap: 14px;
  }
  .count-number { font-weight: 700; font-size: 66px; line-height: 1; }
  .count-unit { font-weight: 700; font-size: 26px; line-height: 28px; letter-spacing: 0.5px; }
  .gold-band {
    position: absolute;
    left: 0; top: 882px;
    width: 100%; height: 50px;
    background: linear-gradient(90deg, var(--gold-light) 0%, var(--gold) 45%, var(--gold-deep) 60%, var(--gold-light) 100%);
  }
</style>
</head>
<body>
  <main class="label">
    <div class="brand">VELANDRA</div>

    <h1 class="product-name">VITALIS</h1>
    <p class="product-phase">RESTORE PHASE 3</p>

    <ul class="features">
      <li>HIGHEST QUALITY ADAPTOGENS</li>
      <li>VITAMIN C AND PANTETHINE ADDED</li>
      <li>MIX OF HERBAL BOTANICALS AND<br>MUSHROOMS</li>
    </ul>

    <div class="brain-art" role="img" aria-label="Gold line illustration of a human brain"></div>

    <p class="supplement-type">DIETARY<br>SUPPLEMENT</p>
    <div class="rule"></div>
    <div class="count">
      <span class="count-number">60</span>
      <span class="count-unit">VEGETABLE<br>CAPSULES</span>
    </div>

    <div class="gold-band"></div>
  </main>
</body>
</html>
```